full stationary design for a modern sleek design company

we are a design company that does modern minimalistic interior design works as well as other design services for high end clients.
we need a full stationary design including and not limited to (double sided business card, letter head, envelopes, documents folder...etc) that reflects the modern style design we do.
sleek modern and minimalistic is the requirements.
Updates

please use the latest attached files as there was a slight modification on the logo Added Wednesday, March 1, 2017

minor update on the logo files in JPG and PSD has been updated kindly follow the new attachments. Added Thursday, March 2, 2017

Target Market(s)

modern minimalist clients

Industry/Entity Type

Design Agency

Requirements
Must have
• the logo
Nice to have
• i like the colors in the colored 3D logo attached
Should not have
• too many colors

```html
<!DOCTYPE html>
<html lang="en">
<head>
<meta charset="utf-8">
<title>Linear Form Studio – Business Card</title>
<link rel="stylesheet" href="https://fonts.googleapis.com/css2?family=Open+Sans:wght@400;600;700&display=swap">
<style>
  :root {
    --backdrop: #e8e5e1;
    --card-light: #ffffff;
    --card-dark: #323535;
    --accent: #f7941d;
    --ink: #4a4a4a;
    --ink-strong: #2f2f2f;
    --logo-light: #ffffff;
  }
  html, body {
    margin: 0;
    padding: 0;
    width: 1200px;
    height: 987px;
    overflow: hidden;
    background: var(--backdrop);
    font-family: "Open Sans", sans-serif;
  }
  .canvas {
    position: relative;
    width: 1200px;
    height: 987px;
  }
  .card {
    position: absolute;
    width: 609px;
    height: 351px;
    box-shadow: 0 3px 8px rgba(0,0,0,0.18);
  }
  .card-front {
    left: 293px;
    top: 130px;
    background: var(--card-light);
    border-radius: 0 176px 176px 0;
  }
  .card-back {
    left: 299px;
    top: 506px;
    background: var(--card-dark);
    border-radius: 176px 0 0 176px;
  }
  .holder {
    position: absolute;
    left: 60px;
    top: 65px;
  }
  .holder-name {
    margin: 0;
    font-size: 24px;
    font-weight: 600;
    color: var(--accent);
    line-height: 1.1;
    letter-spacing: 0.3px;
  }
  .holder-role {
    margin: 2px 0 0;
    font-size: 16.5px;
    color: var(--ink-strong);
  }
  .address {
    margin: 18px 0 0;
    font-size: 16px;
    line-height: 23px;
    color: var(--ink);
    font-style: normal;
  }
  .contacts {
    list-style: none;
    margin: 8px 0 0;
    padding: 0;
  }
  .contacts li {
    display: flex;
    align-items: center;
    height: 23.5px;
    font-size: 16px;
    color: var(--ink);
  }
  .contacts svg {
    width: 15px;
    height: 15px;
    margin-right: 9px;
    flex: none;
  }
  .brand {
    position: absolute;
    left: 0;
    right: 0;
    top: 150px;
    display: flex;
    justify-content: center;
    align-items: center;
    gap: 14px;
  }
  .brand-mark {
    width: 30px;
    height: 30px;
    background: var(--accent);
  }
  .brand-name {
    font-size: 32px;
    font-weight: 600;
    letter-spacing: 3px;
    color: var(--logo-light);
  }
</style>
</head>
<body>
<main class="canvas">
  <section class="card card-front" aria-label="Business card front">
    <div class="holder">
      <h1 class="holder-name">MARLOW KENT</h1>
      <p class="holder-role">CEO&amp;Founder</p>
      <address class="address">214 Willow Crest Road<br>Fairbanks, Alaska 99701</address>
      <ul class="contacts">
        <li>
          <svg viewBox="0 0 16 16" aria-hidden="true"><path fill="#f7941d" d="M3.6 1.2 6 3.6 4.8 5.6c.9 2 2.6 3.7 4.6 4.6l2-1.2 2.4 2.4-1.6 2.6C7.3 13.8 2.2 8.7 1 3z"/></svg>
          (555) 210 4471
        </li>
        <li>
          <svg viewBox="0 0 16 16" aria-hidden="true"><rect x="4" y="1" width="8" height="14" rx="1.5" fill="#f7941d"/><rect x="5.5" y="3" width="5" height="8.5" fill="#fff"/><circle cx="8" cy="13.2" r="0.8" fill="#fff"/></svg>
          (555) 382 9015
        </li>
        <li>
          <svg viewBox="0 0 16 16" aria-hidden="true"><rect x="1.5" y="4" width="13" height="9" fill="#f7941d"/><path d="M1.5 4 8 9l6.5-5" fill="none" stroke="#fff" stroke-width="1"/></svg>
          marlow@linearform.com
        </li>
        <li>
          <svg viewBox="0 0 16 16" aria-hidden="true"><circle cx="8" cy="8" r="6.5" fill="#f7941d"/><path d="M8 1.5v13M1.5 8h13M8 1.5c-3 3.5-3 9.5 0 13M8 1.5c3 3.5 3 9.5 0 13" fill="none" stroke="#fff" stroke-width="0.8"/></svg>
          www.linearform.com
        </li>
      </ul>
    </div>
  </section>

  <section class="card card-back" aria-label="Business card back">
    <div class="brand">
      <span class="brand-mark" aria-hidden="true"></span>
      <span class="brand-name">LINEAR FORM STUDIO</span>
    </div>
  </section>
</main>
</body>
</html>
```